RW Framewell Inc Business cards

We need business cards using our existing logo but slightly modified. Right now the logo says RW Loadbearing Masonry. We want to keep the RW part of the design, but replace the Structural Concrete portion with "FRAMEWELL". Please see the attached file.
Ideally this would be a blank template so we can add Different Names, titles, and phone numbers later.
On the one side we want only the logo and on the other side the detail. I'm attaching an example for you to see.
Please reach out with any other questions. Our address and other details will be given out once we find a design we like.

Target Market(s)

Construction Industry

```html
<!DOCTYPE html>
<html lang="en">
<head>
<meta charset="UTF-8">
<title>RW Framewell Inc – Business Cards</title>
<link rel="stylesheet" href="https://fonts.googleapis.com/css2?family=Archivo:wdth,wght@125,800&family=Arimo:wght@400&display=swap">
<style>
  :root {
    --page-bg: #c9c9c9;
    --brand-blue: #1f73bd;
    --brand-blue-deep: #1b6aae;
    --card-white: #ffffff;
    --panel-grey: #ececec;
    --text-grey: #7a7a7a;
    --logo-grey: #77787b;
  }
  * { margin: 0; padding: 0; box-sizing: border-box; }
  html, body {
    width: 1200px;
    height: 900px;
    overflow: hidden;
    background: var(--page-bg);
  }
  .sheet {
    width: 1200px;
    height: 900px;
    display: flex;
    flex-direction: column;
    align-items: center;
    justify-content: center;
    gap: 44px;
  }
  .card {
    position: relative;
    width: 660px;
    height: 377px;
    border-radius: 30px;
    overflow: hidden;
  }

  /* Front: logo side */
  .card--front {
    background: linear-gradient(135deg, var(--brand-blue) 0%, var(--brand-blue-deep) 55%, var(--brand-blue) 100%);
  }
  .card--front .wordmark {
    position: absolute;
    left: 0; right: 0; top: 0; bottom: 0;
    display: flex;
    align-items: center;
    justify-content: center;
    gap: 18px;
  }
  .wordmark__square {
    width: 34px;
    height: 34px;
    background: var(--card-white);
  }
  .wordmark__name {
    font-family: "Archivo", "Arial Black", sans-serif;
    font-stretch: 125%;
    font-weight: 800;
    font-size: 46px;
    letter-spacing: 1px;
    color: var(--card-white);
    text-transform: uppercase;
  }

  /* Back: detail side */
  .card--back {
    background: var(--card-white);
  }
  .card--back .tone-panel {
    position: absolute;
    top: 0; right: 0;
    width: 300px;
    height: 100%;
    background: linear-gradient(180deg, var(--panel-grey) 0%, #f3f3f3 100%);
  }
  .card--back .wordmark {
    position: absolute;
    left: 46px;
    top: 70px;
    display: flex;
    align-items: center;
    gap: 14px;
  }
  .card--back .wordmark__square { background: var(--brand-blue); width: 28px; height: 28px; }
  .card--back .wordmark__name { color: var(--brand-blue); font-size: 38px; }

  .holder {
    position: absolute;
    left: 46px;
    top: 190px;
  }
  .holder__name {
    font-family: "Archivo", "Arial Black", sans-serif;
    font-stretch: 125%;
    font-weight: 800;
    font-size: 21px;
    color: var(--brand-blue);
    text-transform: uppercase;
    letter-spacing: 0.5px;
  }
  .holder__title {
    font-family: "Arimo", Arial, sans-serif;
    font-size: 18px;
    color: var(--text-grey);
    margin-top: 2px;
  }
  .contact {
    position: absolute;
    left: 46px;
    top: 276px;
    list-style: none;
    font-family: "Arimo", Arial, sans-serif;
    font-size: 17px;
    color: var(--text-grey);
  }
  .contact__item {
    display: flex;
    align-items: center;
    gap: 12px;
    height: 26px;
  }
  .contact__icon { width: 20px; height: 18px; flex: none; }
  .website {
    position: absolute;
    right: 40px;
    bottom: 130px;
    font-family: "Arimo", Arial, sans-serif;
    font-size: 16px;
    color: var(--text-grey);
  }
  .website__domain { color: var(--brand-blue); }
</style>
</head>
<body>
<main class="sheet">
  <section class="card card--front" aria-label="Business card front">
    <div class="wordmark">
      <span class="wordmark__square"></span>
      <span class="wordmark__name">RW Framewell</span>
    </div>
  </section>

  <section class="card card--back" aria-label="Business card back">
    <div class="tone-panel"></div>
    <div class="wordmark">
      <span class="wordmark__square"></span>
      <span class="wordmark__name">RW Framewell</span>
    </div>
    <div class="holder">
      <p class="holder__name">Daniel Harlow</p>
      <p class="holder__title">Managing Director</p>
    </div>
    <ul class="contact">
      <li class="contact__item">
        <svg class="contact__icon" viewBox="0 0 20 18" aria-hidden="true">
          <rect x="1" y="1" width="18" height="16" rx="2" fill="none" stroke="#1f73bd" stroke-width="1.6"/>
          <path d="M6 5c0 4 3 7 8 8l1-2-2-1-1 1c-2-1-3-2-4-4l1-1-1-2z" fill="#1f73bd"/>
        </svg>
        <span>044-555 019 274</span>
      </li>
      <li class="contact__item">
        <svg class="contact__icon" viewBox="0 0 20 18" aria-hidden="true">
          <rect x="1" y="3" width="18" height="12" fill="#1f73bd"/>
          <path d="M1 3l9 7 9-7" fill="none" stroke="#ffffff" stroke-width="1.4"/>
        </svg>
        <span>info@framewellmail.com</span>
      </li>
    </ul>
    <p class="website">www.<span class="website__domain">framewellbuild</span>.com</p>
  </section>
</main>
</body>
</html>
```